Harvest Gateway Fellowship Ministries needs a fresh new web design

We are an up and coming multicultural church that aims to bring people into a life changing encounter with God. We need a fresh and inviting website in order to increase our internet presence and make us easier to connect with.
Here are some of the basic requirements for the site:
• Clearly displayed address, service times, and contact info
• A staff profile page
• An area for a calendar with upcoming events and their details
• Social media buttons
• Group pages for the different ministries (youth, children’s church, men, etc…)
• An area for donations and eCommerce
• A resources page for assorted media (podcasts, sermons, videos, etc.…)
• An area for prayer requests.

```html
<!DOCTYPE html>
<html lang="en">
<head>
<meta charset="utf-8">
<title>Harvest Gateway Fellowship Ministries</title>
<link href="https://fonts.googleapis.com/css2?family=Lato:wght@300;400;700;900&family=Lobster+Two:ital,wght@1,400&display=swap" rel="stylesheet">
<style>
:root{
  --orange:#e2562a;
  --orange-dark:#cf4a21;
  --yellow:#e6c11b;
  --yellow-text:#d9a816;
  --navy:#1f2f8c;
  --ink:#3b3b3b;
  --muted:#6e6e6e;
  --panel:#f1f1f1;
  --white:#ffffff;
  --line:#dcdcdc;
}
*{box-sizing:border-box;margin:0;padding:0}
html,body{width:718px;height:1200px;overflow:hidden}
body{font-family:'Lato',Arial,sans-serif;color:var(--ink);background:var(--panel);position:relative}
.abs{position:absolute}
a{color:inherit;text-decoration:none}

.topbar{left:0;top:0;width:718px;height:24px;background:var(--orange);color:var(--white);font-size:7.5px}
.topbar .tagline{left:60px;top:8px}
.topbar .schedule-label{left:440px;top:8px;font-size:8px}
.topbar .schedule-divider{left:550px;top:4px;width:1px;height:16px;background:var(--white)}
.topbar .schedule-times{left:558px;top:4px;line-height:9px;font-size:6.8px}

.header{left:0;top:24px;width:718px;height:68px;background:var(--white)}
.brand{left:60px;top:14px;display:flex;align-items:center;gap:6px}
.brand-dot{width:26px;height:26px;border-radius:50%;background:var(--yellow)}
.brand-name{font-weight:900;color:var(--navy);font-size:10.5px;line-height:12px;width:118px;text-transform:uppercase}
.info{top:14px;text-align:right;font-size:7.4px;line-height:9px;color:var(--muted)}
.info h4{color:var(--orange);font-size:9.5px;font-weight:700;margin-bottom:3px}
.info .more{color:var(--orange);font-size:7px}
.info-divider{top:16px;width:1px;height:44px;background:var(--line)}
.social-dot{width:16px;height:16px;border-radius:50%;background:#9a9a9a;left:642px}

.nav{left:0;top:92px;width:718px;height:25px;background:var(--yellow);border-bottom:1px solid #c9a40f}
.nav ul{list-style:none;display:flex;justify-content:space-between;padding:0 68px;font-size:8px;color:#5a3e0a;line-height:25px}

.hero{left:0;top:117px;width:718px;height:206px;background:linear-gradient(180deg,#e7e2d5 0%,#efe4c2 40%,#caa64a 70%,#a7791f 100%)}
.hero .feel{left:62px;top:56px;font-family:'Lobster Two',cursive;font-style:italic;color:var(--orange);font-size:15px}
.hero .headline{left:61px;top:73px;font-weight:900;color:var(--orange);font-size:19px;letter-spacing:.2px}
.hero .ofgod{left:266px;top:94px;font-family:'Lobster Two',cursive;font-style:italic;color:var(--orange);font-size:14px}
.hero-arrow{top:86px;width:16px;height:22px;background:rgba(255,255,255,.8);border-radius:50%}

.verse{left:0;top:323px;width:718px;height:57px;background:var(--orange);color:var(--white)}
.verse .label{left:60px;top:19px;font-weight:700;font-size:9px}
.verse .bracket{left:158px;top:14px;width:4px;height:19px;border:1px solid var(--white);border-right:none}
.verse .ref{left:167px;top:14px;font-size:7.6px;line-height:10px}

.features{left:60px;top:368px;width:598px;height:154px;background:var(--white);box-shadow:0 1px 4px rgba(0,0,0,.18);border-radius:3px}
.card{top:375px;width:141px}
.card .photo{height:85px;position:relative;border-radius:2px 2px 0 0;overflow:hidden}
.card .photo .title{position:absolute;left:0;bottom:0;width:100%;height:24px;background:rgba(226,86,42,.92);color:var(--white);font-weight:700;font-size:9.5px;text-align:center;line-height:24px;text-transform:uppercase}
.card p{font-size:7.6px;line-height:11px;text-align:center;color:var(--muted);margin-top:6px}
.card .btn{display:block;width:65px;height:17px;margin:8px auto 0;background:var(--yellow);color:#4a3406;font-size:7.6px;text-align:center;line-height:17px;border-radius:2px}

.rule{left:60px;top:530px;width:598px;height:1px;background:var(--line)}

.section-title{font-weight:300;color:var(--orange);font-size:14px;text-transform:uppercase;padding-bottom:5px;border-bottom:1px solid #e8a58d}
.news-title{left:65px;top:545px;width:378px}
.events-title{left:472px;top:545px;width:186px}

.news{left:65px;width:378px;display:flex;gap:12px}
.news .thumb{width:120px;height:75px;flex:none}
.news h3{font-size:11px;font-weight:700;line-height:12px;color:#333;margin-bottom:3px}
.news p{font-size:7.4px;line-height:12px;color:var(--muted)}
.news .read{color:var(--yellow-text);font-size:7.6px;display:block;margin-top:3px}

.event{left:472px;width:186px;border-bottom:1px solid var(--line);padding-bottom:6px}
.event .date{color:var(--orange);font-size:17px;font-weight:300;line-height:18px}
.event .date b{font-weight:900}
.event h3{font-size:11px;font-weight:700;color:#444;line-height:13px}
.event p{font-size:7.4px;line-height:12px;color:var(--muted)}
.event.active h3,.event.active p{color:var(--yellow-text)}

.map{left:0;top:873px;width:718px;height:149px;background:linear-gradient(135deg,#e9e6dd,#dedbd0 60%,#e6e3d8)}

.footer{left:0;top:1022px;width:718px;height:178px;background:var(--orange);color:var(--white)}
.footer h4{font-weight:300;font-size:11px;text-transform:uppercase;margin-bottom:7px}
.footer .col{top:23px;font-size:7.4px;line-height:11px}
.footer ul{list-style:none}
.footer .contact-line{display:flex;align-items:center;gap:6px;margin-top:3px}
.footer input{width:108px;height:20px;border:none;border-radius:2px;padding-left:7px;font-family:inherit;font-size:7.4px;margin-top:5px}
.footer .subscribe{width:56px;height:20px;margin-top:7px;background:var(--yellow);color:#4a3406;font-size:7.4px;text-align:center;line-height:20px;border-radius:2px}
.footer .ring{width:19px;height:19px;border-radius:50%;background:rgba(255,255,255,.55);display:inline-block;margin-right:5px;margin-top:6px}
.footer .base-rule{left:60px;top:133px;width:598px;height:1px;background:rgba(255,255,255,.3)}
.footer .copyright{left:0;top:142px;width:718px;text-align:center;font-size:7.4px}
</style>
</head>
<body>

<div class="abs topbar">
  <span class="abs tagline">A house of prayer for all nations, where the love, the presence and the power of God are real.</span>
  <span class="abs schedule-label">SUNDAY SERVICE SCHEDULE</span>
  <span class="abs schedule-divider"></span>
  <span class="abs schedule-times">09:00 A.M. | Sunday School<br>10:30 A.M. | Convergent Service</span>
</div>

<header class="abs header">
  <div class="abs brand"><span class="brand-dot"></span><span class="brand-name">Harvest Gateway Fellowship Ministries</span></div>
  <div class="abs info" style="left:245px;width:97px"><h4>Donate</h4>Lorem Ipsum is simply dummy text of the printing<br><a class="more" href="#">Donate Now »</a></div>
  <span class="abs info-divider" style="left:355px"></span>
  <div class="abs info" style="left:363px;width:148px"><h4>Request Prayer</h4>Lorem Ipsum is simply dummy text of the printing and typesetting industry.<br><a class="more" href="#">Request Now »</a></div>
  <span class="abs info-divider" style="left:523px"></span>
  <div class="abs info" style="left:530px;width:87px"><h4>Address</h4>Harvest Gateway<br>City, Location<br><a class="more" href="#">Contact »</a></div>
  <span class="abs social-dot" style="top:17px"></span>
  <span class="abs social-dot" style="top:36px"></span>
</header>

<nav class="abs nav">
  <ul><li>Home</li><li>About</li><li>Staff Profile</li><li>News and Events</li><li>Worship &amp; Services</li><li>Groups</li><li>Shop</li><li>Resources</li><li>Contact</li></ul>
</nav>

<section class="abs hero" role="img" aria-label="Photo of a man with arms raised in a golden wheat field">
  <span class="abs feel">Feel the</span>
  <span class="abs headline">LOVE, PRESENCE &amp; POWER</span>
  <span class="abs ofgod">of God</span>
  <span class="abs hero-arrow" style="left:-8px"></span>
  <span class="abs hero-arrow" style="left:710px"></span>
</section>

<section class="abs verse">
  <span class="abs label">VERSE OF THE DAY</span>
  <span class="abs bracket"></span>
  <span class="abs ref">Romans 5:5 (NIV)<br>And hope does not disappoint us, because God has poured out his love into our hearts by the Holy Spirit, whom he has given us.</span>
</section>

<div class="abs features"></div>
<div class="abs card" style="left:66px">
  <div class="photo" role="img" aria-label="Studio microphone in front of a globe" style="background:linear-gradient(135deg,#2a2a2a,#3c5f86)"><span class="title">Radio Shows</span></div>
  <p>Lorem Ipsum is simply dummy text of the printing and typesetting industry..</p><a class="btn" href="#">Know More</a>
</div>
<div class="abs card" style="left:214px">
  <div class="photo" role="img" aria-label="Church interior with pews and altar" style="background:linear-gradient(180deg,#e8e4e0,#c9b7a8 60%,#b5582f)"><span class="title">Sunday Service</span></div>
  <p>Lorem Ipsum is simply dummy text of the printing and typesetting industry..</p><a class="btn" href="#">Know More</a>
</div>
<div class="abs card" style="left:362px">
  <div class="photo" role="img" aria-label="Hands holding a cardboard donate sign" style="background:linear-gradient(135deg,#8a8a8a,#c8b9a0)"><span class="title">Donate for a Cause</span></div>
  <p>Lorem Ipsum is simply dummy text of the printing and typesetting industry..</p><a class="btn" href="#">Know More</a>
</div>
<div class="abs card" style="left:510px">
  <div class="photo" role="img" aria-label="Hands folded in prayer" style="background:linear-gradient(135deg,#3a2a22,#8d5b44)"><span class="title">Prayer Request</span></div>
  <p>Lorem Ipsum is simply dummy text of the printing and typesetting industry..</p><a class="btn" href="#">Know More</a>
</div>

<div class="abs rule"></div>

<h2 class="abs section-title news-title">Latest News</h2>
<article class="abs news" style="top:583px">
  <div class="thumb" role="img" aria-label="Group of people talking around a table" style="background:linear-gradient(135deg,#c7d3dc,#7c8e9a)"></div>
  <div><h3>Lorem Ipsum is simply dummy text of the printing and typesetting industry.</h3><p>Lorem Ipsum is simply dummy text of the printing and typesetting industry. Lorem Ipsum has been the industry's standard dummy text ever since the 1500s..</p><a class="read" href="#">Read More</a></div>
</article>
<article class="abs news" style="top:675px">
  <div class="thumb" role="img" aria-label="Youth group standing together outdoors" style="background:linear-gradient(135deg,#3d5a3a,#8a7a6a)"></div>
  <div><h3>Lorem Ipsum is simply dummy text.</h3><p>Lorem Ipsum is simply dummy text of the printing and typesetting industry. Lorem Ipsum has been the industry's standard dummy text ever since the 1500s, when an unknown printer took a galley of type and scrambled it to make a type specimen book..</p><a class="read" href="#">Read More</a></div>
</article>
<article class="abs news" style="top:767px">
  <div class="thumb" role="img" aria-label="Lit candles glowing in the dark" style="background:linear-gradient(135deg,#3a1505,#d9701e 60%,#4a1a06)"></div>
  <div><h3>Lorem Ipsum is simply dummy text printing.</h3><p>Lorem Ipsum is simply dummy text of the printing and typesetting industry. Lorem Ipsum has been the industry's standard dummy text ever since the 1500s, when an unknown printer took a galley of type and scrambled it to make a type specimen book..</p><a class="read" href="#">Read More</a></div>
</article>

<h2 class="abs section-title events-title">Upcoming Events</h2>
<div class="abs event" style="top:581px"><div class="date"><b>26</b> JUN</div><h3>Vacation Bible School</h3><p>Lorem Ipsum is simply dummy text of the printing and typesetting industry.</p></div>
<div class="abs event active" style="top:652px"><div class="date"><b>27</b> JUN</div><h3>Vacation Bible School</h3><p>Lorem Ipsum is simply dummy text of the printing and typesetting industry.</p></div>
<div class="abs event" style="top:722px"><div class="date"><b>28</b> JUN</div><h3>Vacation Bible School</h3><p>Lorem Ipsum is simply dummy text of the printing and typesetting industry.</p></div>
<div class="abs event" style="top:793px;border-bottom:none"><div class="date"><b>29</b> JUN</div><h3>Family and Friends Day</h3><p>Sunday June 29th is our family and friends day with special guest pastor Daniel Okafor. Come with faith..</p></div>

<section class="abs map" role="img" aria-label="Road map showing the church location">
  <svg class="abs" style="left:362px;top:52px" width="28" height="36" viewBox="0 0 28 36"><path d="M14 1C7 1 2 6 2 13c0 9 12 22 12 22s12-13 12-22C26 6 21 1 14 1z" fill="#e2562a"/><circle cx="14" cy="13" r="6" fill="#fff"/></svg>
</section>

<footer class="abs footer">
  <div class="abs col" style="left:60px"><h4>Contact Us</h4>Harvest Gateway<br>Location, city<br>State Name, Country
    <div class="contact-line" style="margin-top:9px"><svg width="9" height="9" viewBox="0 0 24 24"><path fill="#fff" d="M6.6 10.8a15.1 15.1 0 006.6 6.6l2.2-2.2c.3-.3.7-.4 1-.2 1.1.4 2.3.6 3.6.6.6 0 1 .4 1 1V20c0 .6-.4 1-1 1A17 17 0 013 4c0-.6.4-1 1-1h3.5c.6 0 1 .4 1 1 0 1.3.2 2.5.6 3.6.1.3 0 .7-.2 1z"/></svg>+1 555-014-2290</div>
    <div class="contact-line"><svg width="9" height="7" viewBox="0 0 24 18"><rect x="1" y="1" width="22" height="16" fill="none" stroke="#fff" stroke-width="2"/><path d="M1 1l11 9 11-9" fill="none" stroke="#fff" stroke-width="2"/></svg>hello@harvestgatewayfm.org</div>
  </div>
  <div class="abs col" style="left:192px"><h4>Communities We Serve</h4>
    <div style="display:flex;gap:12px"><ul><li>• Lorem Ipsum</li><li>• Dummy Links</li><li>• More dummy</li><li>• Sample Text</li><li>• More samples</li></ul><ul><li>• type text dummy</li><li>• Lorem Ipsum</li></ul></div>
  </div>
  <div class="abs col" style="left:358px"><h4>Newsletter</h4>Enter your email below to get notified<br><input type="text" placeholder="Your Email"><div class="subscribe">Subscribe</div></div>
  <div class="abs col" style="left:524px"><h4>Connect With Us</h4>Stay connected for the latest updates at<br>Harvest Gateway Fellowship<br><span class="ring"></span><span class="ring"></span></div>
  <div class="abs base-rule"></div>
  <div class="abs copyright">Copyright © 2014. All rights reserved. Harvest Gateway.</div>
</footer>

</body>
</html>
```